Keystone ridge construction brochure

i would like a brochure that can be send to clients digitally and printed. we are a geotechnical, foundation, and concrete company. I attached info below

Target Market(s)

Construction managers, general contractors, developers, municipalities, private, and commercial partners.

Industry/Entity Type

Geotechnical / foundation

Font styles to use
Serif
Other font styles liked:
• Maybe same as logo

Colors
0054AA
0677BA
7BADD7
CADEEF
E8F1F8

```html
<!DOCTYPE html>
<html lang="en">
<head>
<meta charset="utf-8">
<title>Keystone Ridge Construction Brochure</title>
<link href="https://fonts.googleapis.com/css2?family=Montserrat:wght@300;400;500;600;700;800&display=swap" rel="stylesheet">
<style>
  :root{
    --navy:#0c2757;
    --ink:#1d2433;
    --paper:#ffffff;
    --panel:#f2f3f6;
    --band:#d9dce2;
    --stage:#555555;
    --rule:#9aa6bd;
    --sky-top:#e8f1f8;
    --sky-mid:#dfe8f1;
    --ground:#bba487;
  }
  *{margin:0;padding:0;box-sizing:border-box}
  html,body{width:1200px;height:786px;overflow:hidden;background:var(--stage)}
  body{font-family:'Montserrat',sans-serif;color:var(--ink);position:relative}
  .page{position:absolute;top:41px;width:545px;height:704px;background:var(--paper);overflow:hidden}
  .page--front{left:44px}
  .page--back{left:611px}
  .abs{position:absolute}

  /* front */
  .front-photo{left:0;top:0;width:545px;height:570px;
    background:linear-gradient(180deg,var(--sky-top) 0%,var(--sky-mid) 62%,#c9c2b3 74%,var(--ground) 86%,#a98f70 100%)}
  .brand{left:30px;top:36px;color:var(--navy);font-weight:800;font-size:27px;line-height:30px;letter-spacing:1px}
  .headline{left:30px;top:134px;color:var(--navy)}
  .headline__light{font-weight:300;font-size:31px;line-height:36px;letter-spacing:1px;color:var(--ink)}
  .headline__bold{font-weight:800;font-size:33px;line-height:36px}
  .subhead{left:28px;top:255px;font-size:20px;font-weight:500;color:var(--ink)}
  .accent-rule{left:30px;top:289px;width:191px;height:1px;background:var(--navy)}
  .accent-rule::before{content:"";position:absolute;left:0;top:-2px;width:75px;height:4px;background:var(--navy)}
  .intro{left:30px;top:309px;width:274px;font-size:8.6px;line-height:13.8px;text-align:justify}

  .values{left:0;top:570px;width:545px;height:88px;background:var(--navy);color:#fff}
  .value{position:absolute;top:12px}
  .value svg{display:block;width:20px;height:20px}
  .value__title{font-size:8.6px;font-weight:600;margin-top:10px}
  .value__text{font-size:6.8px;line-height:8.2px;margin-top:4px;color:#e6eaf2}
  .value-divider{position:absolute;top:22px;width:1px;height:43px;background:#8fa0c2}
  .tagline{left:0;top:658px;width:545px;height:46px;background:var(--band);color:var(--navy);
    font-size:13.5px;font-weight:500;letter-spacing:4.3px;text-align:center;line-height:46px}

  /* back */
  .hero{left:0;top:0;width:545px;height:187px;background:var(--navy)}
  .hero__photo{position:absolute;left:0;top:0}
  .hero__text{left:21px;top:56px;color:#fff;font-size:17.5px;line-height:23px;font-weight:400}
  .hero__text b{font-weight:800}
  .info{left:0;top:187px;width:545px;height:285px;background:var(--panel)}
  .section-title{position:absolute;top:18px;font-size:12.8px;font-weight:700;color:var(--navy);letter-spacing:.2px}
  .section-title::after{content:"";position:absolute;left:0;top:21px;width:167px;height:1px;background:var(--navy)}
  .col-divider{left:272px;top:35px;width:1px;height:213px;background:var(--rule)}
  .service{position:absolute;left:20px}
  .service__icon{position:absolute;left:0;top:0;width:42px;height:44px;border-radius:4px;background:var(--navy);display:flex;align-items:center;justify-content:center}
  .service__bar{position:absolute;left:52px;top:0;width:1px;height:44px;background:var(--navy)}
  .service__body{position:absolute;left:62px;top:-3px;width:165px}
  .item-title{font-size:9.2px;font-weight:500;color:var(--navy);letter-spacing:.2px}
  .item-text{font-size:6.8px;line-height:11px;margin-top:3px;color:#333a48}
  .industry{position:absolute;left:301px}
  .industry__icon{position:absolute;left:0;top:0;width:36px;height:36px;border-radius:50%;background:var(--navy);display:flex;align-items:center;justify-content:center}
  .industry__body{position:absolute;left:48px;top:-1px;width:170px}
  .site-photo{left:0;top:472px;width:545px;height:94px;background:linear-gradient(180deg,#c9cacb 0%,#a7a8aa 55%,#4a4b4d 100%)}
  .footer{left:0;top:566px;width:545px;height:134px;background:var(--navy);color:#fff}
  .cta{left:20px;top:18px;font-size:12px;line-height:14.5px;font-weight:400;letter-spacing:.2px}
  .cta b{font-weight:700}
  .contacts{left:20px;top:56px;list-style:none}
  .contacts li{display:flex;align-items:center;height:16.2px;font-size:8.6px}
  .contacts svg{width:8px;height:8px;margin-right:8px;flex:none}
  .footer-brand{left:325px;top:50px;font-weight:800;font-size:19px;line-height:20px;letter-spacing:.5px;text-align:center}
  .footer-divider{left:441px;top:37px;width:1px;height:62px;background:#c8d0e0}
  .footer-tag{left:453px;top:44px;font-size:9px;line-height:11.3px;letter-spacing:1.6px}
  .footer-tag b{display:block;font-weight:700;margin-top:5px}
  .base-strip{left:0;top:700px;width:545px;height:4px;background:var(--band)}
</style>
</head>
<body>

<section class="page page--front">
  <div class="abs front-photo" role="img" aria-label="Photo of a piling rig and excavator on a site of concrete pier foundations with a city skyline behind"></div>
  <div class="abs brand">KEYSTONE<br>RIDGE</div>
  <h1 class="abs headline">
    <div class="headline__light">BUILDING</div>
    <div class="headline__bold">STRONGER</div>
    <div class="headline__bold">FOUNDATIONS</div>
  </h1>
  <div class="abs subhead">FOR A SOLID TOMORROW</div>
  <div class="abs accent-rule"></div>
  <p class="abs intro">At Keystone Ridge, we provide innovative geotechnical, foundation, and concrete solutions that form the base of every successful project. Our commitment to safety, quality, &amp; performance drives everything we do.</p>

  <div class="abs values">
    <div class="value" style="left:19px">
      <svg viewBox="0 0 20 20"><path d="M10 1 L18 4 V10 C18 15 14 18 10 19 C6 18 2 15 2 10 V4 Z" fill="#fff"/><path d="M6.5 10 L9 12.5 L13.5 7.5" stroke="var(--navy)" stroke-width="1.8" fill="none"/></svg>
      <div class="value__title">SAFETY FIRST</div>
      <div class="value__text">Protecting our team, clients,<br>and communities</div>
    </div>
    <div class="value-divider" style="left:134px"></div>
    <div class="value" style="left:152px">
      <svg viewBox="0 0 20 20" fill="#fff"><circle cx="10" cy="5" r="2.6"/><circle cx="4.5" cy="7" r="2"/><circle cx="15.5" cy="7" r="2"/><path d="M5 18 C5 12 15 12 15 18 Z"/><path d="M1 15 C1 10 7 10 7 13 Z"/><path d="M19 15 C19 10 13 10 13 13 Z"/></svg>
      <div class="value__title">EXPERT TEAM</div>
      <div class="value__text">Experienced professionals<br>dedicated to your success</div>
    </div>
    <div class="value-divider" style="left:260px"></div>
    <div class="value" style="left:278px">
      <svg viewBox="0 0 20 20"><circle cx="10" cy="9" r="7" fill="none" stroke="#fff" stroke-width="2"/><path d="M6.5 9 L9 11.5 L14 5.5" stroke="#fff" stroke-width="2" fill="none"/><path d="M6 15 L5 19 L8 17.5 M14 15 L15 19 L12 17.5" stroke="#fff" stroke-width="1.5" fill="none"/></svg>
      <div class="value__title">QUALITY ASSURED</div>
      <div class="value__text">Best materials, advanced<br>techniques, strict quality control</div>
    </div>
    <div class="value-divider" style="left:406px"></div>
    <div class="value" style="left:424px">
      <svg viewBox="0 0 20 20" fill="#fff"><circle cx="5" cy="3.5" r="2"/><circle cx="10" cy="3" r="2"/><circle cx="15" cy="3.5" r="2"/><path d="M2 11 L6 8 L10 11 L14 8 L18 11 L14 17 L10 13 L6 17 Z"/></svg>
      <div class="value__title">CLIENT FOCUSED</div>
      <div class="value__text">Building lasting relationships<br>through trust and results</div>
    </div>
  </div>
  <div class="abs tagline">EXPERIENCE.INTEGRITY.PERFORMANCE.</div>
</section>

<section class="page page--back">
  <div class="abs hero">
    <svg class="hero__photo" width="545" height="187" viewBox="0 0 545 187" role="img" aria-label="Close-up photo of an auger drilling into brown soil beside a tracked rig">
      <defs>
        <linearGradient id="soil" x1="0" y1="0" x2="1" y2="1">
          <stop offset="0" stop-color="#8a7358"/>
          <stop offset=".5" stop-color="#a9784a"/>
          <stop offset="1" stop-color="#6e4a2c"/>
        </linearGradient>
      </defs>
      <polygon points="321,0 545,0 545,187 236,187" fill="url(#soil)"/>
    </svg>
    <div class="abs hero__text">A STRONG<br>FOUNDATION TODAY.<br><b>A BETTER TOMORROW.</b></div>
  </div>

  <div class="abs info">
    <h2 class="section-title" style="left:20px">OUR SERVICES</h2>
    <h2 class="section-title" style="left:301px">INDUSTRIES WE SERVE</h2>
    <div class="abs col-divider"></div>

    <div class="service" style="top:67px">
      <div class="service__icon"><svg width="16" height="26" viewBox="0 0 16 26"><rect x="5" y="1" width="6" height="3" fill="#fff"/><path d="M8 4 V24" stroke="#fff" stroke-width="2"/><path d="M4 8 L12 10 M4 12 L12 14 M4 16 L12 18" stroke="#fff" stroke-width="1.4"/></svg></div>
      <div class="service__bar"></div>
      <div class="service__body">
        <div class="item-title">GEOTECHNICAL SOLUTIONS</div>
        <div class="item-text">Comprehensive site investigations, soil testing, and engineering analysis to mitigate risk and inform smart decisions.</div>
      </div>
    </div>
    <div class="service" style="top:142px">
      <div class="service__icon"><svg width="22" height="22" viewBox="0 0 22 22" fill="#fff"><rect x="9" y="1" width="4" height="11"/><rect x="6" y="5" width="10" height="1.5"/><rect x="6" y="9" width="10" height="1.5"/><rect x="2" y="13" width="18" height="2"/><rect x="3" y="16" width="2" height="5"/><rect x="10" y="16" width="2" height="5"/><rect x="17" y="16" width="2" height="5"/></svg></div>
      <div class="service__bar"></div>
      <div class="service__body">
        <div class="item-title">FOUNDATION SOLUTIONS</div>
        <div class="item-text">Specialized in deep foundations, helical piers, drilled shafts, and retaining systems for projects of any scale</div>
      </div>
    </div>
    <div class="service" style="top:218px">
      <div class="service__icon"><svg width="26" height="26" viewBox="0 0 26 26"><path d="M3 23 L10 13 L14 17 Z" fill="none" stroke="#fff" stroke-width="1.6"/><path d="M12 15 L22 4" stroke="#fff" stroke-width="3" stroke-linecap="round"/></svg></div>
      <div class="service__bar"></div>
      <div class="service__body">
        <div class="item-title">CONCRETE CONSTRUCTION</div>
        <div class="item-text">From structural concrete to flatwork and specialty finishes, we deliver durable and precise concrete solutions.</div>
      </div>
    </div>

    <div class="industry" style="top:66px">
      <div class="industry__icon"><svg width="18" height="18" viewBox="0 0 18 18" fill="#fff"><rect x="2" y="7" width="5" height="10"/><rect x="8" y="2" width="7" height="15"/><rect x="1" y="16.5" width="16" height="1.5"/></svg></div>
      <div class="industry__body">
        <div class="item-title">COMMERCIAL</div>
        <div class="item-text">We prioritize the safety of our team, clients, and communities</div>
      </div>
    </div>
    <div class="industry" style="top:119px">
      <div class="industry__icon"><svg width="18" height="18" viewBox="0 0 18 18" fill="#fff"><path d="M1 17 V8 L6 11 V8 L11 11 V3 H13 V1 H15 V17 Z"/></svg></div>
      <div class="industry__body">
        <div class="item-title">INDUSTRIAL</div>
        <div class="item-text">Skilled professionals with deep industry knowledge and hands-on experience.</div>
      </div>
    </div>
    <div class="industry" style="top:173px">
      <div class="industry__icon"><svg width="18" height="18" viewBox="0 0 18 18" fill="#fff"><rect x="4" y="2" width="1.6" height="15"/><rect x="1" y="3" width="10" height="1.4"/><rect x="10" y="8" width="6" height="9"/></svg></div>
      <div class="industry__body">
        <div class="item-title">INFRASTRUCTURE</div>
        <div class="item-text">We use the best materials, advanced techniques, and strict quality control.</div>
      </div>
    </div>
    <div class="industry" style="top:226px">
      <div class="industry__icon"><svg width="18" height="18" viewBox="0 0 18 18" fill="#fff"><path d="M9 1 L17 8 H15 V17 H3 V8 H1 Z"/></svg></div>
      <div class="industry__body">
        <div class="item-title">RESIDENTIAL</div>
        <div class="item-text">We partner with our clients to build lasting relationships and successful projects.</div>
      </div>
    </div>
  </div>

  <div class="abs site-photo" role="img" aria-label="Black and white photo of a steel building frame under construction with tower cranes"></div>

  <footer class="abs footer">
    <div class="abs cta">LET'S BUILD<br>SOMETHING <b>GREAT TOGETHER.</b></div>
    <ul class="abs contacts">
      <li><svg viewBox="0 0 10 10"><path d="M2 0.5 L4 2.8 L3 4 C3.8 5.6 4.6 6.4 6 7 L7.2 6 L9.5 8 L8 9.6 C4 9 1 6 0.4 2 Z" fill="#fff"/></svg>(555) 014-2280</li>
      <li><svg viewBox="0 0 10 10"><rect x="0.5" y="2" width="9" height="6.5" fill="#fff"/><path d="M0.5 2 L5 5.5 L9.5 2" stroke="var(--navy)" fill="none"/></svg>info@keystoneridgebuild.com</li>
      <li><svg viewBox="0 0 10 10" fill="none" stroke="#fff"><circle cx="5" cy="5" r="4.3"/><ellipse cx="5" cy="5" rx="1.8" ry="4.3"/><path d="M0.7 5 H9.3"/></svg>www.keystoneridgebuild.com</li>
      <li><svg viewBox="0 0 10 10"><path d="M5 0.5 C7.3 0.5 8.5 2.2 8.5 4 C8.5 6.2 5 9.6 5 9.6 C5 9.6 1.5 6.2 1.5 4 C1.5 2.2 2.7 0.5 5 0.5 Z" fill="#fff"/><circle cx="5" cy="4" r="1.3" fill="var(--navy)"/></svg>Cedar Hollow, Texas</li>
    </ul>
    <svg class="abs" style="left:240px;top:18px" width="60" height="104" viewBox="0 0 60 104"><line x1="56" y1="2" x2="4" y2="102" stroke="#7f8fae" stroke-width="1.5"/></svg>
    <div class="abs footer-brand">KEYSTONE<br>RIDGE</div>
    <div class="abs footer-divider"></div>
    <div class="abs footer-tag">ANCHORING<br>YOUR VISION<b>DELIVERING<br>EXCELLENCE.</b></div>
  </footer>
  <div class="abs base-strip"></div>
</section>

</body>
</html>
```